Velmora Consulting Business

** Please add the content information from my old business card
1. I would like to see a two sided business card with both options with the 1st Option--Tallow Spire-new WHITE BACKGROUND LOGO
2 nd Option-Tallow Spire - new BLACK- Background Logo
3rd -Option a business card with my Photo on the card
Please add the new word to the card information:
EXECUTION
AS THE OWNER'S REP
WE AIM TO ACHIEVE YOUR
INFRASTRUCTURE VISION with
OUR SPECIALIZATION & EXECUTION in:

FUNDING Planning
BUSINESS Planning
INFRASTRUCTURE Planning
PROJECT Management
Since 2012
_____________________________________________________________________
I want to get spot uv raised printing. I was liking a a nice rich white linen paper stock with black writing & NOT A COLORED CARD other than a variety of white or black cards concept

```html
<!DOCTYPE html>
<html lang="en">
<head>
<meta charset="utf-8">
<title>Velmora Consulting – Business Card</title>
<link rel="stylesheet" href="https://fonts.googleapis.com/css2?family=Open+Sans:wght@400;600;700&display=swap">
<style>
  :root {
    --stage: #1c1c1d;
    --card-black: #231f20;
    --card-white: #f4f4f2;
    --ink: #111111;
    --ink-soft: #2b2b2b;
    --paper-text: #ffffff;
    --accent-red: #e21b35;
    --mark-grey: #bdbdbd;
    --mark-dark: #3a3637;
  }
  * { box-sizing: border-box; margin: 0; padding: 0; }
  html, body { width: 1200px; height: 1015px; overflow: hidden; }
  body {
    background: var(--stage);
    font-family: "Open Sans", Arial, sans-serif;
    position: relative;
  }
  .card {
    position: absolute;
    width: 525px;
    height: 300px;
    box-shadow: 0 12px 30px rgba(0,0,0,.55);
    display: flex;
    flex-direction: column;
    align-items: center;
    text-align: center;
  }
  .card--back {
    left: 90px; top: 150px;
    background: var(--card-black);
    color: var(--paper-text);
    padding-top: 62px;
  }
  .card--front {
    left: 585px; top: 555px;
    background: var(--card-white);
    color: var(--ink);
    padding-top: 56px;
  }
  .brand {
    display: flex;
    align-items: center;
    gap: 10px;
    font-weight: 600;
    font-size: 30px;
    letter-spacing: 1px;
    line-height: 1;
  }
  .brand__dot {
    width: 12px; height: 12px;
    border-radius: 50%;
    background: var(--accent-red);
  }
  .card--back .brand__name { color: var(--mark-dark); }
  .card--front .brand__name { color: var(--mark-grey); }
  .mission {
    margin-top: 26px;
    font-size: 12px;
    line-height: 1.3;
    text-transform: uppercase;
  }
  .services {
    margin-top: 14px;
    font-size: 12px;
    line-height: 1.35;
  }
  .services__bar { color: var(--accent-red); padding: 0 3px; }
  .since { font-size: 12px; margin-top: 2px; }
  .person__name {
    margin-top: 34px;
    font-weight: 700;
    font-size: 20px;
    line-height: 1.1;
  }
  .person__title {
    font-size: 12px;
    text-transform: uppercase;
    color: var(--ink-soft);
  }
  .rule {
    width: 60px; height: 1px;
    background: var(--accent-red);
    margin: 10px auto 10px;
  }
  .locations, .email { font-size: 13px; line-height: 1.45; }
  .contact-row {
    position: absolute;
    left: 22px; right: 22px; bottom: 20px;
    display: flex;
    justify-content: space-between;
    font-size: 13px;
  }
  .label { font-weight: 700; }
</style>
</head>
<body>

  <section class="card card--back" aria-label="Card back">
    <div class="brand"><span class="brand__name">Velmora Consulting</span><span class="brand__dot"></span></div>
    <p class="mission">
      Execution as the owner's rep<br>
      We aim to achieve your infrastructure vision <span style="text-transform:none">with</span><br>
      our specialization &amp; execution <span style="text-transform:none">in:</span>
    </p>
    <p class="services">
      FUNDING Planning<span class="services__bar">|</span>BUSINESS Planning<br>
      INFRASTRUCTURE Planning<span class="services__bar">|</span>PROJECT Management
    </p>
    <p class="since">Since 2012</p>
  </section>

  <section class="card card--front" aria-label="Card front">
    <div class="brand"><span class="brand__name">Velmora Consulting</span><span class="brand__dot"></span></div>
    <h1 class="person__name">Renata Holloway-Marsh</h1>
    <p class="person__title">CEO / Lead Project Manager</p>
    <div class="rule"></div>
    <p class="locations">Northgate NT • Brookhaven NB</p>
    <div class="contact-row">
      <span><span class="label">P:</span> 555.210.4478</span>
      <span><span class="label">E:</span> renata@velmora.ca</span>
      <span><span class="label">W:</span> www.velmora.ca</span>
    </div>
  </section>

</body>
</html>
```